Jewelers Website

This is for the DESIGN ONLY.
I am a software programmer and will be doing the development.
New website design for
www.lunacrestgems.com.au
Need a fresh new look for an online only jewellery business who produce their jewellery by hand. I would like it designed in a parallax style. Feel free to recommend fonts to use for the site. This is an Australian based company located in NSW so shots of sites in NSW might make nice background images.
http://vornaplex.me/demo/#theme=parallax
To contain the below sections
About Us
Contact Us
Gallery
Testimonials
Diamond Types
The colour scheme is to be Black / White and Silver.
With the Parallax style there will be moving sections and images for added impact.
Target Market(s)
Young Adults mainly engagement jewellery

```html
<!DOCTYPE html>
<html lang="en">
<head>
<meta charset="utf-8">
<title>Lunacrest Gems</title>
<link rel="stylesheet" href="https://fonts.googleapis.com/css2?family=Montserrat:wght@400;600;700&family=Lato:wght@400;700&family=Cormorant+Garamond:wght@500&display=swap">
<style>
:root{
  --black:#0b0b0b;
  --ink:#1c1c1c;
  --dark:#2a2a2a;
  --white:#ffffff;
  --silver:#c9c9c9;
  --silver-light:#ececec;
  --field:#f2f2f2;
  --field-line:#dcdcdc;
  --muted:#9a9a9a;
  --name:#2c3e6b;
}
*{margin:0;padding:0;box-sizing:border-box}
html,body{width:1200px;height:2871px;overflow:hidden;background:var(--white)}
body{font-family:"Lato",sans-serif;color:var(--ink);position:relative}
.abs{position:absolute}
.heading{font-family:"Montserrat",sans-serif;color:var(--ink)}

/* hero */
.hero{left:0;top:0;width:1200px;height:598px;background:radial-gradient(ellipse at 55% 35%,#4a4a4a 0%,#1e1e1e 45%,#050505 100%)}
.nav a{position:absolute;top:64px;font-family:"Montserrat",sans-serif;font-size:12px;color:var(--white);text-decoration:none;letter-spacing:.3px}
.brand{left:470px;top:36px;width:260px;text-align:center;font-family:"Montserrat",sans-serif;font-weight:400;color:var(--white);font-size:25px;line-height:29px;letter-spacing:1px}
.hero-title{left:0;top:208px;width:1200px;text-align:center;font-family:"Montserrat",sans-serif;font-weight:700;color:var(--white);font-size:46px;line-height:54px}
.hero-sub{left:0;top:333px;width:1200px;text-align:center;color:var(--white);font-size:12px}
.btn-outline{left:525px;top:388px;width:160px;height:38px;border:1px solid var(--white);border-radius:3px;color:var(--white);font-family:"Montserrat",sans-serif;font-size:14px;display:flex;align-items:center;justify-content:center}

/* who we are */
.who-title{left:138px;top:645px;font-size:32px;font-weight:400;letter-spacing:.5px}
.who-text{left:138px;top:696px;width:610px;font-size:12.5px;line-height:20px;color:var(--ink)}
.btn-dark{background:var(--dark);color:var(--white);font-family:"Montserrat",sans-serif;display:flex;align-items:center;justify-content:center;border-radius:2px}
.who-btn{left:138px;top:858px;width:168px;height:39px;font-size:15px;gap:12px}
.ring{left:805px;top:630px;width:275px;height:290px;background:radial-gradient(circle at 50% 40%,#ffffff 0%,#e4e4e4 55%,#ffffff 80%)}

/* diamond types */
.types{left:0;top:1008px;width:1200px;height:396px;background:linear-gradient(180deg,#9c9c9c 0%,#d8d8d8 45%,#c4c4c4 100%)}
.types-photo{left:120px;top:1060px;width:400px;height:270px;background:radial-gradient(ellipse at 45% 55%,#f4f4f4 0%,#bdbdbd 55%,rgba(190,190,190,0) 80%)}
.types-title{left:604px;top:1036px;font-size:22px;font-weight:600}
.types-intro{left:606px;top:1078px;width:452px;font-size:10.5px;line-height:15px;color:var(--ink)}
.ticks{left:612px;top:1148px;width:460px;list-style:none}
.ticks li{display:flex;align-items:center;gap:14px;height:28px;font-size:11.5px;color:var(--ink)}
.types-btn{left:616px;top:1330px;width:138px;height:28px;font-size:12px;background:#111}

/* gallery */
.gallery{left:0;top:1404px;width:1200px;height:556px;background:#eeeeee}
.gallery-title{left:0;top:1424px;width:1200px;text-align:center;font-size:32px;font-weight:400}
.photo{box-shadow:4px 6px 10px rgba(0,0,0,.35)}
.caption{font-family:"Lato",sans-serif;font-weight:700;font-size:14.5px;color:var(--black);text-align:center;width:204px}

/* testimonials */
.testi{left:0;top:1960px;width:1200px;height:406px;background:radial-gradient(ellipse at 50% 40%,#d4d4d4 0%,#bebebe 60%,#a9a9a9 100%)}
.testi-title{left:0;top:2004px;width:1200px;text-align:center;font-size:24px;font-weight:600}
.avatar{left:553px;top:2074px;width:94px;height:94px;border-radius:50%;border:3px solid var(--white);background:radial-gradient(circle at 50% 45%,#f0d7b8,#c89a6a)}
.quote{font-family:"Cormorant Garamond",serif;font-size:110px;color:rgba(255,255,255,.55);line-height:1}
.testi-text{left:185px;top:2196px;width:830px;text-align:center;font-size:14px;line-height:21px;color:var(--black)}
.testi-rule{left:435px;top:2277px;width:330px;height:1px;background:var(--ink)}
.testi-name{left:0;top:2300px;width:1200px;text-align:center;font-family:"Cormorant Garamond",serif;font-weight:500;font-size:24px;color:var(--name)}

/* contact */
.contact-title{left:0;top:2408px;width:1200px;text-align:center;font-size:24px;font-weight:600}
.contact-sub{left:280px;top:2466px;width:640px;text-align:center;font-size:11px;line-height:18px;color:var(--muted)}
.field{background:var(--field);border:2px solid var(--field-line);font-family:"Montserrat",sans-serif;font-size:11px;color:#c2c2c2;padding:14px 12px;letter-spacing:.5px}
.send{left:528px;top:2750px;width:136px;height:30px;font-size:13px;font-weight:600;background:#1a1a1a}

/* footer */
.footer{left:0;top:2838px;width:1200px;height:33px;background:var(--black);color:#bdbdbd;font-size:10.5px}
.footer span{position:absolute;top:10px}
</style>
</head>
<body>

<section class="abs hero" role="img" aria-label="Black and white photo of a woman wearing a diamond necklace and bracelet with soft bokeh lights"></section>
<nav class="nav">
  <a style="left:138px">HOME</a>
  <a style="left:201px">ABOUT US</a>
  <a style="left:285px">DIAMOND TYPES</a>
  <a style="left:765px">GALLERY</a>
  <a style="left:851px">TESTIMONIALS</a>
  <a style="left:989px">CONTACT US</a>
</nav>
<div class="abs brand">LUNACREST<br>GEMS</div>
<h1 class="abs hero-title">WELLCOME TO THE<br>LUNACREST GEMS</h1>
<p class="abs hero-sub">Loremt ipsum dolor sit amet elit, sed do Ut enim ad minim veniam. Lorem adipisicing elit</p>
<div class="abs btn-outline">Read More</div>

<h2 class="abs heading who-title">WHO WE ARE</h2>
<p class="abs who-text">Lorem ipsum dolor sit amet, consectetur adipisicing elit, sed do eiusmod tempor incididunt ut labore etLorem ipsum dolor sit amet, consectetur adipisicing elit, sed do eiusmod tempor .incididunt ut labore etLorem ipsum dolor sit amet, consectetur adipisicing elit, sed do eiuts mod tempor incididunt ut labore etLorem ipsum dolor sit amet, consectetur adipisicing elit, sed do eiusmod tempor .incididunt ut labore et Lorem ipsum dolor sit amet, consectetur adipisicing elit, sed od tempor incididunt ut labore etLorem ipsum dolor sit amet, consectetur adipisicing elit, sed do eiusmod tempor .incididunt ut labore et</p>
<div class="abs btn-dark who-btn">
  <svg width="18" height="16" viewBox="0 0 18 16"><path d="M4 1h10l3 4-8 10L1 5z" fill="none" stroke="#fff" stroke-width="1.6"/><path d="M1 5h16M6 1l3 14 3-14" fill="none" stroke="#fff" stroke-width="1.2"/></svg>
  Read More
</div>
<div class="abs ring" role="img" aria-label="Silver engagement ring with a large cushion cut diamond"></div>

<section class="abs types"></section>
<div class="abs types-photo" role="img" aria-label="Three loose cut diamonds on a silver surface"></div>
<h2 class="abs heading types-title">TYPE OF DIAMONDS</h2>
<p class="abs types-intro">Sed ut perspiciatis unde omnis iste natus error sit voluptatem accusantium doloremque laudantium, totam rem aperiam, eaque ipsa quae ab illo inventore veritatis et quasi archit ecto beatae vitae dicta sunt explicabo</p>
<ul class="abs ticks">
  <li><svg width="16" height="14" viewBox="0 0 16 14"><path d="M1 7l5 5L15 1" fill="none" stroke="#111" stroke-width="3"/></svg>Sed ut perspiciatis unde omnis iste natus error sit totam rem aperiam, eaque</li>
  <li><svg width="16" height="14" viewBox="0 0 16 14"><path d="M1 7l5 5L15 1" fill="none" stroke="#111" stroke-width="3"/></svg>ipsa quae ab illo inventore veritatis et quasi architecto beatae vitae dicta sunt</li>
  <li><svg width="16" height="14" viewBox="0 0 16 14"><path d="M1 7l5 5L15 1" fill="none" stroke="#111" stroke-width="3"/></svg>explicabo. Nemo enim ipsam voluptatem quia voluptas sit aspernatur aut odit</li>
  <li><svg width="16" height="14" viewBox="0 0 16 14"><path d="M1 7l5 5L15 1" fill="none" stroke="#111" stroke-width="3"/></svg>aut fugit, sed quia consequuntur magni dolores eos qui ratione voluptatem</li>
  <li><svg width="16" height="14" viewBox="0 0 16 14"><path d="M1 7l5 5L15 1" fill="none" stroke="#111" stroke-width="3"/></svg>sequi nesciunt. Neque porro quisquam est, qui dolorem ipsum quia dolor sit</li>
  <li><svg width="16" height="14" viewBox="0 0 16 14"><path d="M1 7l5 5L15 1" fill="none" stroke="#111" stroke-width="3"/></svg>amet, consectetur, adipisci velit, sed quia non numquam eius modi tempora</li>
</ul>
<div class="abs btn-dark types-btn">Read More</div>

<section class="abs gallery" role="img" aria-label="Soft white painted brick wall background"></section>
<h2 class="abs heading gallery-title">OUR GALLERY</h2>
<div class="abs photo" style="left:185px;top:1523px;width:204px;height:129px;background:linear-gradient(135deg,#3a2a24,#7a5a48 50%,#1a1412)" role="img" aria-label="Woman wearing a jewelled ring and bracelet"></div>
<div class="abs caption" style="left:185px;top:1671px">LOREM IPSUM DOLOR</div>
<div class="abs photo" style="left:185px;top:1744px;width:204px;height:122px;background:linear-gradient(135deg,#e8e8e8,#8a8a8a 55%,#2a2a2a)" role="img" aria-label="Woman in profile wearing drop earrings and a necklace"></div>
<div class="abs caption" style="left:185px;top:1886px">LOREM IPSUM DOLOR</div>
<div class="abs photo" style="left:480px;top:1523px;width:204px;height:299px;background:linear-gradient(180deg,#5a4636 0%,#c49a7a 45%,#f0ebe6 75%,#ffffff)" role="img" aria-label="Close-up of an eye with a diamond themed script caption"></div>
<div class="abs caption" style="left:480px;top:1850px">LOREM IPSUM DOLOR</div>
<div class="abs photo" style="left:776px;top:1523px;width:204px;height:137px;background:linear-gradient(135deg,#5a1e18,#b06a58 50%,#3a1010)" role="img" aria-label="Diamond necklace held against a red background"></div>
<div class="abs caption" style="left:776px;top:1679px">LOREM IPSUM DOLOR</div>
<div class="abs photo" style="left:776px;top:1750px;width:204px;height:143px;background:linear-gradient(135deg,#1a1a1a,#6a4a3a 50%,#111)" role="img" aria-label="Smiling woman with long hair wearing diamond earrings"></div>
<div class="abs caption" style="left:776px;top:1913px">LOREM IPSUM DOLOR</div>

<section class="abs testi" role="img" aria-label="Faded black and white photo of a woman with bokeh lights"></section>
<h2 class="abs heading testi-title">TESTIMONIALS</h2>
<div class="abs avatar" role="img" aria-label="Portrait of the reviewer"></div>
<div class="abs quote" style="left:140px;top:2120px">&ldquo;</div>
<div class="abs quote" style="left:1010px;top:2120px">&rdquo;</div>
<p class="abs testi-text">Lorem ipsum dolor sit amet, consectetur adipisicing elit, sed do eiusmod tempor incididunt ut labore et dolore magna aliqua. Ut enim ad minim veniam, quis nostrud exercitation ullamco laboris nisi ut aliquip ex ea commodo consequat. Duis aute irure dolor in reprehenderit in voluptate velit esse cillum dolore eu fugiat nulla pariatur..</p>
<div class="abs testi-rule"></div>
<div class="abs testi-name">Dario Velluti, CEO</div>

<h2 class="abs heading contact-title">CONTACT US</h2>
<p class="abs contact-sub">Sed ut perspiciatis unde omnis iste natus error sit voluptatem accusantium doloremque laudantium, totam rem aperiam, eaque ipsa quae ab illo inventore veritatis et quasi architecto beatae vitae dicta sunt explicabo</p>
<div class="abs field" style="left:138px;top:2540px;width:428px;height:45px">NAME</div>
<div class="abs field" style="left:138px;top:2604px;width:428px;height:45px">EMAIL</div>
<div class="abs field" style="left:138px;top:2669px;width:428px;height:45px">PHONE</div>
<div class="abs field" style="left:595px;top:2540px;width:465px;height:174px">MESSAGE</div>
<div class="abs btn-dark send">SEND MESSAGE</div>

<footer class="abs footer">
  <span style="left:138px">Copyrights © 2014 lunacrestgems.com - All Rights Reserved</span>
  <span style="left:894px">Privacy Policy &nbsp; | &nbsp; Terms of Uses</span>
</footer>

</body>
</html>
```